real esate business card with company logo and name

we need a business card design for a real esate company

The company name is Walsh & Brand Pty Ltd, and we have our logo designed and will upload. We want classic or moden feel. Black or white background. looks more textured. Should include folowinginformations
Owen Walsh and Lucy Brand
Sales Agents & Onsite Manager
p: 07 5948 2063
F: 07 5948 2174
M:0431 857 219
3/42 Marlow Crescent, FERNLEA QLD 4213

We want this business card looks professonal. Thank you in advance.

Industry/Entity Type

Real Estate Agent

Contact Information for Business Card

Owen Walsh and Lucy Brand
Onsite Manager & Sales Agents
p: 07 5948 2063
M:0431 857 219

Font styles to use
Serif

Colors
000000
fbfbfb
333333
959595

Requirements
Must have
• company logo and name, black or white back ground

```html
<!DOCTYPE html>
<html lang="en">
<head>
<meta charset="utf-8">
<title>Walsh &amp; Brand Pty Ltd – Business Card</title>
<link rel="stylesheet" href="https://fonts.googleapis.com/css2?family=Merriweather:wght@300;400&family=Montserrat:wght@400&display=swap">
<style>
  :root {
    --ink: #000000;
    --paper: #fbfbfb;
    --charcoal: #333333;
    --silver: #959595;
    --stage: #e4e4e4;
  }
  * { box-sizing: border-box; margin: 0; padding: 0; }
  html, body { width: 1200px; height: 913px; overflow: hidden; }
  body {
    background: var(--stage);
    position: relative;
    font-family: "Merriweather", Georgia, serif;
  }
  .card {
    position: absolute;
    width: 560px;
    height: 320px;
    border-radius: 4px;
    background: radial-gradient(ellipse at 40% 30%, #1e1e1e 0%, #0b0b0b 55%, var(--ink) 100%);
    box-shadow: 0 18px 40px rgba(0,0,0,.35);
    overflow: hidden;
  }
  .card--front { left: 60px; top: 90px; }
  .card--back  { left: 580px; top: 500px; }

  /* Front */
  .brand {
    position: absolute;
    left: 36px; top: 0; width: 210px; height: 100%;
    display: flex; align-items: center; justify-content: center;
    gap: 10px;
  }
  .brand__dot {
    width: 10px; height: 10px; border-radius: 50%;
    background: var(--silver); flex: none;
  }
  .brand__name {
    font-family: "Montserrat", Arial, sans-serif;
    font-size: 14px; letter-spacing: 1.5px;
    text-transform: uppercase;
    color: var(--silver);
    white-space: nowrap;
  }
  .divider {
    position: absolute;
    left: 262px; top: 50px; width: 1px; height: 220px;
    background: var(--charcoal);
  }
  .details {
    position: absolute;
    left: 290px; top: 62px; right: 24px;
    color: var(--paper);
  }
  .details__names { font-size: 19px; font-weight: 400; line-height: 1.2; }
  .details__role { font-size: 12px; font-weight: 300; color: var(--silver); margin-top: 4px; }
  .details__address { font-size: 12.5px; font-weight: 300; line-height: 1.45; margin-top: 14px; }
  .contact { list-style: none; margin-top: 14px; }
  .contact li {
    display: flex; align-items: center; gap: 9px;
    font-size: 12.5px; font-weight: 300; line-height: 1.7;
  }
  .contact svg { width: 11px; height: 11px; fill: var(--silver); flex: none; }

  /* Back */
  .card--back .brand {
    left: 0; width: 100%;
    gap: 14px;
  }
  .card--back .brand__dot { width: 14px; height: 14px; }
  .card--back .brand__name { font-size: 22px; letter-spacing: 2.5px; }
</style>
</head>
<body>

<section class="card card--front" aria-label="Business card front">
  <div class="brand">
    <span class="brand__dot"></span>
    <span class="brand__name">Walsh &amp; Brand Pty Ltd</span>
  </div>
  <div class="divider"></div>
  <div class="details">
    <h1 class="details__names">Owen Walsh &amp; Lucy Brand</h1>
    <p class="details__role">Sales Agents &amp; Onsite Manager</p>
    <p class="details__address">3/42 Marlow Crescent,<br>FERNLEA QLD 4213</p>
    <ul class="contact">
      <li>
        <svg viewBox="0 0 24 24" aria-label="Phone"><path d="M6.6 10.8a15 15 0 0 0 6.6 6.6l2.2-2.2c.3-.3.7-.4 1-.2 1.1.4 2.3.6 3.6.6.6 0 1 .4 1 1V20c0 .6-.4 1-1 1A17 17 0 0 1 3 4c0-.6.4-1 1-1h3.5c.6 0 1 .4 1 1 0 1.3.2 2.5.6 3.6.1.3 0 .7-.2 1z"/></svg>
        07 5948 2063
      </li>
      <li>
        <svg viewBox="0 0 24 24" aria-label="Fax"><path d="M6 2h9l3 3v5H6zM3 11h18v9H3zm3 3v2h4v-2zm8 0v2h4v-2z"/></svg>
        07 5948 2174
      </li>
      <li>
        <svg viewBox="0 0 24 24" aria-label="Mobile"><path d="M7 1h10a2 2 0 0 1 2 2v18a2 2 0 0 1-2 2H7a2 2 0 0 1-2-2V3a2 2 0 0 1 2-2zm0 3v14h10V4zm5 15.5a1 1 0 1 0 0 2 1 1 0 0 0 0-2z"/></svg>
        0431 857 219
      </li>
    </ul>
  </div>
</section>

<section class="card card--back" aria-label="Business card back">
  <div class="brand">
    <span class="brand__dot"></span>
    <span class="brand__name">Walsh &amp; Brand Pty Ltd</span>
  </div>
</section>

</body>
</html>
```